Lumora Drink Mix Packaging Design

We need a packaging design for our new product called "Lumora Drink Mix." This drink mix can help prevent hangovers or lessen their severity if consumed after a night of drinking. Our tagline is: "Feel as good tomorrow morning as you do tonight." Our website is www.lumoradrinkmix-example.com. We are looking for a design that includes an outer box that contains individual serving packets and the packets themselves. Background color should be black and the colors should be vibrant. Our website uses bright blues, pinks, and purples reminiscent of colors under a blacklight (think club). Our target audience is 30-35 year-old people that occasionally party like they're still 18-21, but then regret it the following day. Please reference our website for additional information on the product.

Target Market(s)

Target market is 30-35 year old men and women that occasionally drink like they're still 18-21.

Industry/Entity Type

Product

Requirements
Must have
• Project must include a box that can hold ~5 individual serving packets inside, as well as the packets inside. Box must contain nutritional information and obligatory NQB disclaimer on one panel, as must the back of the single-serving packets. Package must be black as background with vibrant colors that "pop" and catch someone's eye. Package must include the product name "Lumora Drink Mix." Package must include the company name "Lumora Products, Inc."
Nice to have
• It should convey fun, friendship, partying, but also safety. Ideally, the tagline: "Feel as good tomorrow morning as you do tonight" should be somewhere on the packaging.
Should not have
• Pictures of people.

```html
<!DOCTYPE html>
<html lang="en">
<head>
<meta charset="utf-8">
<title>Lumora Drink Mix Packaging</title>
<link rel="stylesheet" href="https://fonts.googleapis.com/css2?family=Oswald:wght@300;400;700&family=Roboto:wght@400;700&display=swap">
<style>
  :root {
    --canvas: #ffffff;
    --black: #050506;
    --box-grey: #333335;
    --panel-inner: #141416;
    --cyan: #2aa6dc;
    --magenta: #f01df0;
    --red: #ff0a0a;
    --white: #ffffff;
    --teal: #1f9f8f;
    --sky: #7fd6f0;
    --blue: #2f5fd0;
    --violet: #9a3fd8;
    --ink: #1a1a1a;
  }
  * { box-sizing: border-box; margin: 0; padding: 0; }
  html, body { width: 1200px; height: 1140px; overflow: hidden; background: var(--canvas); }
  .canvas { position: relative; width: 1200px; height: 1140px; font-family: "Oswald", sans-serif; }

  .glow-band {
    position: absolute; left: 0; right: 0;
    background:
      radial-gradient(ellipse 40% 70% at 45% 50%, rgba(220,245,255,.85), transparent 70%),
      linear-gradient(90deg, var(--teal) 0%, var(--sky) 35%, var(--blue) 75%, var(--violet) 100%);
  }

  /* outer box */
  .box { position: absolute; top: 40px; left: 360px; display: flex; gap: 10px; }
  .box-front, .box-side { position: relative; height: 500px; background: var(--box-grey); overflow: hidden; }
  .box-front { width: 300px; }
  .box-side { width: 170px; display: flex; flex-direction: column; align-items: center; justify-content: center; }
  .box-front .glow-band.top { top: 0; height: 70px; }
  .box-front .glow-band.bottom { top: 330px; bottom: 0; }
  .box-front .tagline-tri { position: absolute; left: 12px; top: 60px; width: 130px; }
  .box-front .brand { position: absolute; left: 50px; top: 158px; width: 240px; }
  .box-front .brand-company { font-size: 14px; }
  .box-front .brand-name { font-size: 48px; margin-top: 2px; line-height: .92; }

  /* packets */
  .packet { position: absolute; top: 605px; width: 505px; height: 505px; background: var(--black); overflow: hidden; }
  .packet.front { left: 112px; }
  .packet.back { left: 665px; }
  .packet .glow-band.top { top: 0; height: 116px; }
  .packet .glow-band.bottom { top: 418px; height: 87px; }
  .packet .window {
    position: absolute; left: 48px; right: 48px; top: 116px; height: 302px;
    background: linear-gradient(90deg, var(--black), var(--panel-inner) 12%, var(--panel-inner) 88%, var(--black));
  }
  .packet .hang-notch { position: absolute; right: -14px; top: 40px; width: 28px; height: 28px; border-radius: 50%; background: var(--canvas); }
  .packet .tagline-tri { position: absolute; left: 58px; top: 46px; width: 156px; }

  .brand { text-align: center; }
  .brand-company { color: var(--magenta); font-weight: 400; font-size: 17px; letter-spacing: .2px; text-transform: uppercase; }
  .brand-name {
    color: var(--cyan); font-family: "Oswald", sans-serif; font-weight: 700;
    text-transform: lowercase; line-height: .95; font-size: 62px; margin-top: 6px;
  }
  .packet.front .brand { position: absolute; left: 150px; top: 150px; width: 310px; }
  .packet.front .brand-name { font-size: 76px; }
  .box-side .brand-company { font-size: 12px; }
  .box-side .brand-name { font-size: 40px; }

  .tri-text { font-family: "Oswald", sans-serif; font-weight: 300; fill: var(--white); text-anchor: middle; }

  /* back packet */
  .claim {
    position: absolute; top: 62px; left: 0; right: 0; text-align: center;
    color: var(--ink); font-weight: 300; font-size: 12.5px; line-height: 1.35; text-transform: uppercase;
  }
  .nutrition {
    position: absolute; left: 130px; top: 130px; width: 248px; height: 278px;
    border: 2px solid var(--white); border-radius: 10px; background: var(--black);
    color: var(--white); padding: 16px 20px 10px; font-family: "Roboto", sans-serif;
  }
  .nutrition h2 { font-family: "Oswald", sans-serif; font-weight: 400; font-size: 31px; line-height: 1; border-top: 2px solid var(--white); border-bottom: 2px solid var(--white); padding: 4px 0 2px; text-align: center; }
  .nutrition .row { display: flex; justify-content: space-between; font-size: 5.5px; border-bottom: .5px solid #bbb; padding: 2px 0; }
  .nutrition .serving { display: flex; font-size: 7px; border-bottom: 2px solid var(--white); }
  .nutrition .serving span { flex: 1; padding: 3px 2px; }
  .nutrition .serving span + span { border-left: 1px solid var(--white); }
  .nutrition .dv { text-align: right; font-size: 5.5px; font-weight: 700; border-bottom: .5px solid #bbb; padding: 3px 0; border-top: 1px solid var(--white); margin-top: 6px; }
  .nutrition .vitamins { display: flex; border-top: 2px solid var(--white); margin-top: 10px; }
  .nutrition .vitamins > div { flex: 1; }
  .nutrition .vitamins > div + div { border-left: 1px solid var(--white); padding-left: 3px; }
  .nutrition .vitamins > div:first-child { padding-right: 3px; }
  .nutrition .note { font-size: 5px; line-height: 1.3; margin-top: 4px; border-top: 1px solid var(--white); padding-top: 3px; }
  .agency { position: absolute; left: 392px; top: 378px; color: var(--white); font-weight: 400; font-size: 20px; }
</style>
</head>
<body>
<div class="canvas">

  <div class="box">
    <section class="box-front">
      <div class="glow-band top" role="img" aria-label="Soft blurred blacklight glow in teal, blue and violet"></div>
      <div class="glow-band bottom" role="img" aria-label="Soft blurred blacklight glow with bokeh light spots in teal, blue and violet"></div>
      <svg class="tagline-tri" viewBox="0 0 130 112" aria-label="Feel as good tomorrow morning as you do tonight.">
        <polygon points="0,0 130,0 65,112" fill="var(--red)"/>
        <text class="tri-text" font-size="9.5"><tspan x="65" y="20">FEEL AS GOOD</tspan><tspan x="65" y="33">TOMORROW MORNING</tspan><tspan x="65" y="46">AS YOU DO</tspan><tspan x="65" y="59">TONIGHT.</tspan></text>
      </svg>
      <div class="brand">
        <p class="brand-company">Lumora Products, Inc.</p>
        <p class="brand-name">lumora<br>drink<br>mix</p>
      </div>
    </section>
    <section class="box-side">
      <div class="brand">
        <p class="brand-company">Lumora Products, Inc.</p>
        <p class="brand-name">lumora<br>drink<br>mix</p>
      </div>
    </section>
  </div>

  <section class="packet front">
    <div class="glow-band top" role="img" aria-label="Soft blurred blacklight glow in teal, blue and violet"></div>
    <div class="window" role="img" aria-label="Dark window with faint bokeh light spots"></div>
    <div class="glow-band bottom" role="img" aria-label="Soft blurred blacklight glow in teal, blue and violet"></div>
    <span class="hang-notch"></span>
    <svg class="tagline-tri" viewBox="0 0 156 136" aria-label="Feel as good tomorrow morning as you do tonight.">
      <polygon points="0,0 156,0 78,136" fill="var(--red)"/>
      <text class="tri-text" font-size="11.5"><tspan x="78" y="26">FEEL AS GOOD</tspan><tspan x="78" y="42">TOMORROW MORNING</tspan><tspan x="78" y="58">AS YOU DO</tspan><tspan x="78" y="74">TONIGHT.</tspan></text>
    </svg>
    <div class="brand">
      <p class="brand-company">Lumora Products, Inc.</p>
      <p class="brand-name">lumora<br>drink<br>mix</p>
    </div>
  </section>

  <section class="packet back">
    <div class="glow-band top" role="img" aria-label="Soft blurred blacklight glow in teal, blue and violet"></div>
    <div class="window" role="img" aria-label="Dark window with faint bokeh light spots"></div>
    <div class="glow-band bottom" role="img" aria-label="Soft blurred blacklight glow in teal, blue and violet"></div>
    <span class="hang-notch"></span>
    <p class="claim">This drink mix can help prevent<br>hangovers or lessen their severity if<br>consumed after a night of drinking</p>
    <div class="nutrition">
      <h2>NUTRITION FACTS</h2>
      <div class="serving"><span>Serving size</span><span>Serving per Container</span></div>
      <div class="serving"><span>Amount per serving</span><span>Calories</span></div>
      <div class="dv">% Daily Value*</div>
      <div class="row"><span>Total fat</span><span>...g</span><span>...%</span></div>
      <div class="row"><span>Saturated fat</span><span>...g</span><span>...%</span></div>
      <div class="row"><span>Cholesterol</span><span>...g</span><span>...%</span></div>
      <div class="row"><span>Sodium</span><span>...g</span><span>...%</span></div>
      <div class="row"><span>Total carbohydrate</span><span>...g</span><span>...%</span></div>
      <div class="row"><span>Dietary Fiber</span><span>...g</span><span>...%</span></div>
      <div class="row"><span>Sugar</span><span>...g</span><span>...%</span></div>
      <div class="row"><span>Protein</span><span>...g</span><span>...%</span></div>
      <div class="vitamins">
        <div><div class="row"><span>Vitamin A</span><span>...%</span></div><div class="row"><span>Calcium</span><span>...%</span></div></div>
        <div><div class="row"><span>Vitamin C</span><span>...%</span></div><div class="row"><span>Iron</span><span>...%</span></div></div>
      </div>
      <p class="note">*Percent Daily Values are based on 2,000 calorie diet. Your daily values may be higher or lower depending on your calorie needs.</p>
    </div>
    <p class="agency">NQB</p>
  </section>

</div>
</body>
</html>
```